Small Business Broker Business Card Design

A business card design for a small business brokerage, which is a financial service, not unlike real estate brokerage, but for small businesses such as laundromats, pizza shops, restaurants, cleaners etc. The designs should all be simple, more conservative in nature, using the colors and font of the logo. Again, think real estate Brokerage as a business context
Contact Information for Business Card
Name: Glen R. Harlow. Title: Small Business Advisor. Email: g.harlow@bayfieldcapitalworks.example. Mobile: (555) 274-3918. Office: (555) 806-2147. www.bayfieldcapitalworks.example

```html
<!DOCTYPE html>
<html lang="en">
<head>
<meta charset="utf-8">
<title>Bayfield Capital Works – Business Card</title>
<link rel="stylesheet" href="https://fonts.googleapis.com/css2?family=Roboto:wght@400;700&family=Roboto+Condensed:wght@400;700&display=swap">
<style>
  :root {
    --stage: #232323;
    --card-dark: #1e1e1e;
    --navy: #173a6e;
    --navy-deep: #12305c;
    --blue: #1f4f99;
    --green: #7dc242;
    --white: #ffffff;
    --line: #9a9a9a;
  }
  * { box-sizing: border-box; margin: 0; padding: 0; }
  html, body { width: 1200px; height: 780px; overflow: hidden; }
  body {
    background: var(--stage);
    position: relative;
    font-family: "Roboto", Arial, sans-serif;
  }
  .card {
    position: absolute;
    top: 236px;
    width: 540px;
    height: 308px;
    border-radius: 3px;
    box-shadow: 0 10px 28px rgba(0,0,0,.55);
    overflow: hidden;
  }
  .card--front { left: 40px; background: var(--card-dark); }
  .card--back { left: 620px; background: var(--navy); }

  /* front: brand block */
  .brand {
    position: absolute;
    top: 58px; left: 0; right: 0;
    text-align: center;
  }
  .brand__row {
    display: inline-flex;
    align-items: center;
    gap: 10px;
  }
  .brand__mark {
    width: 22px; height: 22px;
    background: var(--green);
  }
  .brand__name {
    font-family: "Roboto", Arial, sans-serif;
    font-weight: 700;
    font-size: 22px;
    letter-spacing: 1.5px;
    color: var(--blue);
    text-transform: uppercase;
  }
  .brand__tagline {
    margin-top: 8px;
    font-weight: 700;
    font-size: 10.5px;
    letter-spacing: 2.2px;
    color: var(--green);
    text-transform: uppercase;
  }

  /* front: person */
  .person {
    position: absolute;
    left: 70px;
    top: 196px;
    width: 200px;
    text-align: right;
  }
  .person__name {
    font-family: "Roboto Condensed", "Arial Narrow", sans-serif;
    font-weight: 700;
    font-size: 30px;
    color: var(--green);
    line-height: 1;
  }
  .person__title {
    margin-top: 5px;
    font-family: "Roboto Condensed", "Arial Narrow", sans-serif;
    font-size: 15px;
    color: var(--white);
  }

  .divider {
    position: absolute;
    left: 288px;
    top: 178px;
    width: 1px;
    height: 92px;
    background: var(--line);
  }

  /* front: contact list */
  .contacts {
    position: absolute;
    left: 304px;
    top: 184px;
    list-style: none;
  }
  .contacts__item {
    display: flex;
    align-items: center;
    gap: 8px;
    height: 20px;
    font-family: "Roboto Condensed", "Arial Narrow", sans-serif;
    font-size: 13px;
    color: var(--white);
    white-space: nowrap;
  }
  .contacts__icon { width: 13px; height: 13px; flex: none; }

  /* back */
  .back__pattern {
    position: absolute; inset: 0;
    background: linear-gradient(135deg, var(--navy) 0%, var(--navy-deep) 100%);
  }
  .back__brand {
    position: absolute;
    right: 60px;
    top: 118px;
    display: flex;
    flex-direction: column;
    align-items: center;
    gap: 4px;
  }
  .back__name {
    font-weight: 700;
    font-size: 11px;
    letter-spacing: 1px;
    color: var(--white);
    text-transform: uppercase;
  }
  .back__tagline {
    font-size: 6px;
    letter-spacing: .8px;
    color: var(--white);
    text-transform: uppercase;
  }
</style>
</head>
<body>

<section class="card card--front" aria-label="Business card front">
  <div class="brand">
    <div class="brand__row">
      <span class="brand__mark"></span>
      <span class="brand__name">Bayfield Capital Works, Inc</span>
    </div>
    <p class="brand__tagline">Confidently buy or sell a local business today</p>
  </div>

  <div class="person">
    <h1 class="person__name">Glen R. Harlow</h1>
    <p class="person__title">Small Business Advisor</p>
  </div>

  <div class="divider"></div>

  <ul class="contacts">
    <li class="contacts__item">
      <svg class="contacts__icon" viewBox="0 0 14 14" aria-hidden="true"><rect x="3.5" y="1" width="7" height="12" rx="1.2" fill="none" stroke="var(--blue)" stroke-width="1.3"/><circle cx="7" cy="11" r=".8" fill="var(--blue)"/></svg>
      (555) 274-3918
    </li>
    <li class="contacts__item">
      <svg class="contacts__icon" viewBox="0 0 14 14" aria-hidden="true"><path d="M3 1.5l2.2 2.6-1.2 1.6c.8 1.7 2.2 3.1 3.9 3.9l1.6-1.2 2.6 2.2-1.3 1.8C6 12.2 1.8 8 1.3 2.9z" fill="var(--green)"/></svg>
      (555) 806-2147
    </li>
    <li class="contacts__item">
      <svg class="contacts__icon" viewBox="0 0 14 14" aria-hidden="true"><circle cx="7" cy="7" r="5.8" fill="var(--blue)"/><path d="M1.2 7h11.6M7 1.2c-2.4 3-2.4 8.6 0 11.6M7 1.2c2.4 3 2.4 8.6 0 11.6" stroke="var(--card-dark)" stroke-width=".8" fill="none"/></svg>
      www.bayfieldcapitalworks.example
    </li>
    <li class="contacts__item">
      <svg class="contacts__icon" viewBox="0 0 14 14" aria-hidden="true"><rect x="1" y="3" width="12" height="8.5" rx="1" fill="var(--green)"/><path d="M1.3 3.5L7 8l5.7-4.5" stroke="var(--card-dark)" stroke-width="1" fill="none"/></svg>
      g.harlow@bayfieldcapitalworks.example
    </li>
  </ul>
</section>

<section class="card card--back" aria-label="Business card back">
  <div class="back__pattern" role="img" aria-label="Repeating embossed brand pattern in tones of blue"></div>
  <div class="back__brand">
    <span class="back__name">Bayfield Capital Works, Inc</span>
    <span class="back__tagline">Confidently buy or sell a local business today</span>
  </div>
</section>

</body>
</html>
```